Internal web page of multinational company - Portfolio of reports

We need to improve the look & feel of an existing internal HTML page.
We use it as a portfolios where users go and see a list of existing reports as "tiles". The HTML page is automatically generated by a javascript that reads the contents to display from an HTML file.
What is needs is a "face lift" in the design of the page.
Currently we use icons on the top right of each tile to denote the type of technology used on the report and also colons for the same purpose. The attached screenshots will be self explanatory.
Across the top we have "tabs" that, once selected change the tiles.
Need a proposal for new design that keeps is as clean as possible, specially the home page that should be very light (Plimbo like).
The idea for this page is to serve as a "one stop shop" and become a bookmark for everyone in the company.
Looking for a wow effect that make is visually

Target Market(s)

Internal employees

Industry/Entity Type

It Company

Coding

Coded - Design and coding required

Number of Pages Required

2 page

Requirements
Must have
• Should not change the logo or its position from the bottom left.
• Page must be as clean as possible and
Nice to have
• Welcome to change the logo on the top left. This page is from the CSU M&I (Mni) which stands for Central Support Unit - Metrics & Insight.
Should not have
• Do no use red, this is the color of our competitor. The blue on the bottom is standard for our logo

```html
<!DOCTYPE html>
<html lang="en">
<head>
<meta charset="utf-8">
<title>CSU M&amp;I – Report Portfolio</title>
<link rel="stylesheet" href="https://fonts.googleapis.com/css2?family=Roboto+Condensed:wght@700&family=Roboto:wght@400;500&display=swap">
<style>
  :root {
    --brand-blue: #0055a6;
    --text-dark: #4d4d4d;
    --text-muted: #8c8c8c;
    --white: #ffffff;
    --tile-hr: #6dcff6;
    --tile-finance: #0071bc;
    --tile-ps: #003471;
    --tile-csu: #0d004c;
    --tile-distribution: #32004b;
    --footer-bg: #363636;
    --footer-accent: #262626;
    --footer-text: #a6a6a6;
  }
  * { margin: 0; padding: 0; box-sizing: border-box; }
  html, body { width: 1200px; height: 658px; overflow: hidden; }
  body {
    position: relative;
    background: var(--white);
    font-family: "Roboto", Arial, sans-serif;
    color: var(--text-dark);
  }
  .site-header {
    position: absolute; left: 0; top: 0; width: 1200px; height: 69px;
    background: var(--brand-blue);
  }
  .brand-name {
    position: absolute; left: 98px; top: 13px;
    font-family: "Roboto Condensed", "Arial Narrow", sans-serif;
    font-weight: 700; font-size: 38px; line-height: 44px;
    color: var(--white);
  }
  .search-box {
    position: absolute; left: 907px; top: 19px; width: 194px; height: 31px;
    background: var(--white); border-radius: 3px;
    display: flex; align-items: center; padding: 0 8px;
  }
  .search-clear { width: 11px; height: 11px; margin-right: 6px; }
  .search-label { flex: 1; font-size: 11px; color: var(--text-muted); }
  .search-icon { width: 15px; height: 15px; }

  .intro { position: absolute; left: 0; top: 200px; width: 1200px; text-align: center; }
  .intro-title {
    font-family: "Roboto Condensed", "Arial Narrow", sans-serif;
    font-weight: 700; font-size: 34px; line-height: 44px; color: var(--text-dark);
  }
  .intro-text { font-size: 13.5px; margin-top: 3px; color: var(--text-dark); }

  .tile-list { position: absolute; left: 98px; top: 315px; display: flex; gap: 31.7px; list-style: none; }
  .tile {
    width: 175px; height: 141px; border-radius: 3px;
    display: flex; flex-direction: column; align-items: center;
    padding-top: 28px; color: var(--white);
  }
  .tile-icon { width: 48px; height: 44px; }
  .tile-label {
    margin-top: 14px;
    font-family: "Roboto Condensed", "Arial Narrow", sans-serif;
    font-weight: 700; font-size: 20.5px; letter-spacing: 0.6px;
  }
  .tile--hr { background: var(--tile-hr); }
  .tile--finance { background: var(--tile-finance); }
  .tile--ps { background: var(--tile-ps); }
  .tile--csu { background: var(--tile-csu); }
  .tile--distribution { background: var(--tile-distribution); }

  .site-footer {
    position: absolute; left: 0; top: 590px; width: 1200px; height: 68px;
    background: var(--footer-bg);
  }
  .feedback-link {
    position: absolute; left: 98px; top: 0; width: 194px; height: 68px;
    background: var(--footer-accent);
    display: flex; align-items: center; padding-left: 22px; gap: 10px;
    font-family: "Roboto Condensed", "Arial Narrow", sans-serif;
    font-weight: 700; font-size: 14px; color: var(--footer-text);
  }
  .feedback-icon { width: 27px; height: 23px; }
  .copyright {
    position: absolute; right: 100px; top: 28px;
    font-size: 10px; color: var(--footer-text); word-spacing: 2px;
  }
</style>
</head>
<body>
  <header class="site-header">
    <div class="brand-name">CSU M&amp;I</div>
    <div class="search-box">
      <svg class="search-clear" viewBox="0 0 10 10"><path d="M1 1L9 9M9 1L1 9" stroke="#c8c8c8" stroke-width="2.4" stroke-linecap="round"/></svg>
      <span class="search-label">Search</span>
      <svg class="search-icon" viewBox="0 0 16 16"><circle cx="6.5" cy="6.5" r="4.8" fill="none" stroke="#777" stroke-width="2.2"/><path d="M10 10L14.5 14.5" stroke="#777" stroke-width="2.6" stroke-linecap="round"/></svg>
    </div>
  </header>

  <main>
    <section class="intro">
      <h1 class="intro-title">Proin a dolor mauris</h1>
      <p class="intro-text">Aenean sed quam non sapien faucibus consequat vitae sit amet orci tellus finibus fermentum</p>
    </section>

    <ul class="tile-list">
      <li class="tile tile--hr">
        <svg class="tile-icon" viewBox="0 0 48 44" fill="#fff">
          <circle cx="11" cy="9" r="6"/><circle cx="37" cy="9" r="6"/>
          <path d="M2 30c0-9 4-13 9-13s7 2 7 2v12H4a2 2 0 0 1-2-1z"/>
          <path d="M46 30c0-9-4-13-9-13s-7 2-7 2v12h14a2 2 0 0 0 2-1z"/>
          <circle cx="24" cy="14" r="8" stroke="var(--tile-hr)" stroke-width="1.5"/>
          <path d="M11 40c0-11 6-16 13-16s13 5 13 16a3 3 0 0 1-3 3H14a3 3 0 0 1-3-3z" stroke="var(--tile-hr)" stroke-width="1.5"/>
        </svg>
        <span class="tile-label">HR</span>
      </li>
      <li class="tile tile--finance">
        <svg class="tile-icon" viewBox="0 0 48 44">
          <rect x="1" y="7" width="46" height="30" fill="#fff"/>
          <path d="M6 12h36v20H6z M6 12a5 5 0 0 1-0 0" fill="var(--tile-finance)"/>
          <circle cx="24" cy="22" r="9" fill="#fff"/>
          <text x="24" y="27" text-anchor="middle" font-family="Roboto, Arial, sans-serif" font-weight="700" font-size="14" fill="var(--tile-finance)">1</text>
        </svg>
        <span class="tile-label">FINANCE</span>
      </li>
      <li class="tile tile--ps">
        <svg class="tile-icon" viewBox="0 0 48 44">
          <path d="M9 2h30v22c0 9-8 15-15 19C17 39 9 33 9 24z" fill="#fff"/>
          <path d="M24 7h10v17c0 6-5 10-10 13z" fill="var(--tile-ps)"/>
        </svg>
        <span class="tile-label">CSU</span>
      </li>
      <li class="tile tile--csu">
        <svg class="tile-icon" viewBox="0 0 48 44" fill="none" stroke="#fff" stroke-width="3.2">
          <path d="M30 8H10a5 5 0 0 0-5 5v22a5 5 0 0 0 5 5h22a5 5 0 0 0 5-5V25"/>
          <path d="M40 3l5 5-18 18-7 2 2-7z" fill="#fff" stroke="none"/>
          <path d="M36 7l5 5" stroke="var(--tile-csu)" stroke-width="1.6"/>
        </svg>
        <span class="tile-label">P&amp;S</span>
      </li>
      <li class="tile tile--distribution">
        <svg class="tile-icon" viewBox="0 0 48 44" fill="#fff">
          <rect x="18" y="1" width="12" height="11" rx="2"/>
          <path d="M24 12v9M9 29v-8h30v8M24 21v8" fill="none" stroke="#fff" stroke-width="3"/>
          <rect x="2" y="29" width="13" height="12" rx="2"/><rect x="18" y="29" width="12" height="12" rx="2"/><rect x="33" y="29" width="13" height="12" rx="2"/>
        </svg>
        <span class="tile-label">DISTRIBUTION</span>
      </li>
    </ul>
  </main>

  <footer class="site-footer">
    <div class="feedback-link">
      <svg class="feedback-icon" viewBox="0 0 28 24" fill="none" stroke="#a6a6a6" stroke-width="2"><path d="M14 2C7 2 2 6 2 11c0 3 2 5 4 6l-2 5 6-3.5c1 .3 2.6.5 4 .5 7 0 12-4 12-8.5S21 2 14 2z"/></svg>
      <span>HELP &amp; FEEDBACK</span>
    </div>
    <p class="copyright">Copyright &copy; 2015 CSU-M&amp;I.&nbsp; All rights reserved.</p>
  </footer>
</body>
</html>
```